New Business Card Design for Manufacturing

We are an engineering/manufacturing company that offers Advanced machining/assembly/engineering services, as well as innovative products for the heavy duty engine cooling markets.

We are looking to get a new business card designed that is clean and modern looking, but still fits the wide range of technical/skilled work we do.

- We hope to use this design as the base for other design work in new Presentations, web, and print work.

Industry/Entity Type

Engineering

Contact Information for Business Card

Our preferred color of blue is (RGB) 22/71/159 but can vary slightly from that color. Our content will be our Logo and full company name (Vantrell Forge Works, Inc.), company address, name, job title, phone number with extension, cell number, fax number, website, and email address on the cards.
We'd like the full company name next to the logo, but we are open to other interpretations of that layout.
Preferably, we would like the back side to be clean with just our logo, and the front to contain all of the contact information.

Colors
2f74b4
0355a3
85abd2

Requirements
Must have
• - Logo, company name, needed content - We are open to interpretation beyond that.
• - Standard size business card.
• - Horizontal orientation.
• - Enough space for lengthy names / job titles (for example, a job title could read "Directory of Human Resources" or "V.P. of Governmental Affairs"). We need this to look clean, whether the title be short (CEO) or long (as described above).

```html
<!DOCTYPE html>
<html lang="en">
<head>
<meta charset="utf-8">
<title>Vantrell Forge Works – Business Card</title>
<link href="https://fonts.googleapis.com/css2?family=Roboto:wght@400;500;700;900&family=Roboto+Condensed:wght@500&display=swap" rel="stylesheet">
<style>
  :root {
    --brand-blue: #0f52a2;
    --ink: #1e1e1e;
    --muted: #555a60;
    --rule: #c9c9c9;
    --card-white: #f6f6f6;
    --stage: #e4e4e4;
  }
  * { margin: 0; padding: 0; box-sizing: border-box; }
  html, body { width: 1200px; height: 960px; overflow: hidden; }
  body {
    background: var(--stage);
    font-family: "Roboto", Arial, sans-serif;
    position: relative;
  }
  .card {
    position: absolute;
    width: 600px;
    height: 342px;
    border-radius: 22px;
    box-shadow: 0 3px 8px rgba(0,0,0,.22);
  }
  .card--front { left: 302px; top: 129px; background: var(--card-white); }
  .card--back  { left: 299px; top: 489px; background: var(--brand-blue); }

  .wordmark {
    position: absolute;
    display: flex;
    align-items: center;
    gap: 10px;
    font-weight: 900;
    letter-spacing: 0;
    line-height: 1;
    white-space: nowrap;
  }
  .wordmark__square { width: 24px; height: 24px; flex: none; }
  .card--front .wordmark { left: 56px; top: 153px; font-size: 36px; color: var(--brand-blue); }
  .card--front .wordmark__square { background: var(--brand-blue); }

  .divider {
    position: absolute;
    left: 309px; top: 86px;
    width: 1px; height: 180px;
    background: var(--rule);
  }
  .contact { position: absolute; left: 337px; top: 86px; }
  .contact__name {
    font-family: "Roboto Condensed", Arial, sans-serif;
    font-weight: 500;
    font-size: 26px;
    color: var(--brand-blue);
    line-height: 1;
  }
  .contact__title { font-size: 15px; color: var(--ink); margin-top: 5px; }
  .contact__address { font-size: 14px; color: var(--muted); margin-top: 10px; line-height: 19px; }
  .contact__list { list-style: none; margin-top: 10px; font-size: 14px; color: var(--muted); }
  .contact__list li { display: flex; align-items: center; height: 19px; }
  .contact__list svg { width: 12px; height: 12px; margin-right: 9px; fill: var(--brand-blue); flex: none; }

  .card--back .wordmark { left: 100px; top: 148px; font-size: 36px; color: #ffffff; }
  .card--back .wordmark__square { background: #ffffff; }
  .company-name {
    position: absolute;
    left: 347px; top: 134px;
    color: #ffffff;
    font-weight: 700;
    font-size: 17px;
    line-height: 19px;
    text-transform: uppercase;
    white-space: nowrap;
  }
</style>
</head>
<body>
  <section class="card card--front" aria-label="Card front">
    <div class="wordmark"><span class="wordmark__square"></span><span>VANTRELL</span></div>
    <div class="divider"></div>
    <div class="contact">
      <h1 class="contact__name">DORIAN KESSLER</h1>
      <p class="contact__title">V.P. of Governmental Affairs</p>
      <p class="contact__address">4210 Larkspur Road<br>Fairbanks, Alaska 34612</p>
      <ul class="contact__list">
        <li><svg viewBox="0 0 24 24"><path d="M6.6 10.8a15 15 0 0 0 6.6 6.6l2.2-2.2c.3-.3.7-.4 1-.2 1.1.4 2.3.6 3.6.6.6 0 1 .4 1 1V20c0 .6-.4 1-1 1A17 17 0 0 1 3 4c0-.6.4-1 1-1h3.5c.6 0 1 .4 1 1 0 1.3.2 2.5.6 3.6.1.3 0 .7-.2 1z"/></svg>689 555 0142</li>
        <li><svg viewBox="0 0 24 24"><path d="M7 1h10a2 2 0 0 1 2 2v18a2 2 0 0 1-2 2H7a2 2 0 0 1-2-2V3a2 2 0 0 1 2-2zm0 3v14h10V4zm5 15.5a1 1 0 1 0 0 2 1 1 0 0 0 0-2z"/></svg>836 555 0178</li>
        <li><svg viewBox="0 0 24 24"><path d="M2 5h20v14H2zm2 2v.5l8 5 8-5V7zm0 2.8V17h16V9.8l-8 5z"/></svg>dorian@vantrellforge.com</li>
        <li><svg viewBox="0 0 24 24"><circle cx="12" cy="12" r="10"/></svg>www.vantrellforge.com</li>
      </ul>
    </div>
  </section>

  <section class="card card--back" aria-label="Card back">
    <div class="wordmark"><span class="wordmark__square"></span><span>VANTRELL</span></div>
    <p class="company-name">Vantrell<br>Forge Works,<br>Inc.</p>
  </section>
</body>
</html>
```